New Alcoholic Spiked Seltzer Line

We need a can design for a line of low calorie alcoholic seltzer. This product is a sparkling water and vodka drink with no sugar added in a slim 12 oz can.

This is a lighter, healthier, alternative to the sugary ready-to-drinks on the market. The product contains only 3 ingredients: Vodka, Water and Natural Flavors. It has only 100 calories but still has 5% alcohol, so you don't need to sacrifice alcohol to cut calories.

This product also does not contain any preservatives.

We want this design to communicate the following objectives to the consumer and in this order:

1. Appetizing product
2.Low calorie
3.Communicate the type of beverage (Spiked Seltzer)

The brand name of the product is VELKA.

The flavor of the product needed to be used for the design is Mango-Orange.

Comparable products are:

www.brindlefizzworks.example/
https://www.quorvabubbles.example
https://pelnavo.example/

The designs should not infringe or copy the creative directions of the products mentionned above. They are only given so that you can better understand the type of product we are developing.

Target Market(s)

Young Professional women between the ages of 25 and 44

Industry/Entity Type

Product

Colors

Designer to choose colors to be used in the design.

Requirements
Must have
• Design extendibility, meaning it can be adapted for other flavors.
• This is a new category in the market we are targeting, so consumers must easily be able to identify what type of product this is.

```html
<!DOCTYPE html>
<html lang="en">
<head>
<meta charset="utf-8">
<title>VELKA Mango-Orange Spiked Seltzer Can Label</title>
<link rel="stylesheet" href="https://fonts.googleapis.com/css2?family=Montserrat:wght@300;400;500;800&display=swap">
<style>
  :root {
    --label-white: #ffffff;
    --mango: #f29a1c;
    --mango-deep: #e8901a;
    --mango-soft: #f6c27a;
    --ink: #2e2e2e;
    --ink-soft: #3a3a3a;
  }
  html, body {
    margin: 0;
    padding: 0;
    width: 1200px;
    height: 2277px;
    overflow: hidden;
    background: var(--label-white);
  }
  .can-label {
    position: relative;
    width: 1200px;
    height: 2277px;
    background: var(--label-white);
    font-family: "Montserrat", Arial, sans-serif;
    overflow: hidden;
  }
  .brand-name {
    position: absolute;
    top: 660px;
    left: 0;
    width: 100%;
    margin: 0;
    text-align: center;
    font-weight: 800;
    font-size: 270px;
    line-height: 1;
    letter-spacing: 4px;
    color: var(--mango);
  }
  .tagline {
    position: absolute;
    top: 1050px;
    left: 0;
    width: 100%;
    margin: 0;
    text-align: center;
    color: var(--mango);
    font-size: 56px;
    font-weight: 800;
    letter-spacing: 1px;
  }
  .tagline .tagline-small {
    font-weight: 400;
    font-size: 40px;
  }
  .calorie-claim {
    position: absolute;
    top: 1270px;
    left: 0;
    width: 100%;
    margin: 0;
    text-align: center;
    color: var(--ink-soft);
    font-weight: 300;
    line-height: 1.05;
  }
  .calorie-claim span { display: block; }
  .calorie-claim .claim-line { font-size: 54px; letter-spacing: 1px; }
  .calorie-claim .claim-emphasis { font-size: 74px; font-weight: 400; color: var(--ink); }
  .claim-small { font-size: 46px !important; }
  .bubble-fade {
    position: absolute;
    left: 0;
    bottom: 0;
    width: 100%;
    height: 920px;
    background: linear-gradient(180deg,
      rgba(255,255,255,0) 0%,
      rgba(246,194,122,0.35) 35%,
      var(--mango-soft) 62%,
      var(--mango-deep) 100%);
  }
  .flavor-name {
    position: absolute;
    top: 1910px;
    left: 0;
    width: 100%;
    margin: 0;
    text-align: center;
    color: var(--label-white);
    font-weight: 800;
    font-size: 54px;
    letter-spacing: 1px;
  }
</style>
</head>
<body>
  <main class="can-label">
    <div class="bubble-fade" role="img" aria-label="Rising carbonation bubbles over a mango-orange colour fade"></div>
    <h1 class="brand-name">VELKA</h1>
    <p class="tagline">SPARKLE <span class="tagline-small">WITH A</span> PUNCH</p>
    <p class="calorie-claim">
      <span class="claim-line">GREAT TASTE</span>
      <span class="claim-line claim-emphasis">WITHOUT</span>
      <span class="claim-line claim-small">THE CALORIES</span>
    </p>
    <p class="flavor-name">MANGO-ORANGE</p>
  </main>
</body>
</html>
```